Patent Law

Need to develop a home page for a patent lawyer.

Colors should go with logo, blues...

Company Name- Velun Tresk, PLLC

Company Overview-

I am an Intellectual Property Lawyer and focus on patents, copyrights, trademarks, & trade secrets. I work with small businesses and start ups in the chemical and biotech industries.

Why Us-

I am small firm that can provide large-firm service at a reasonable price. I also can charge flat-fees for entreprenuers in certain practice areas.

Services-
Intellectual Property
Patents
Copyrights
Trademarks
Trade secrets
Healthcare Compliance
Elder law
Wills
Trusts

Website we like-
http://www.quorvantlegal.example/ - within industry!!
http://www.daltrowemiko.example/
http://ulbrixtane.example/
http://thegravelcounsel.example/

Target Market(s)

My customers will be small business, specifically small start-up companies in the chemical and biotech arena.

Industry/Entity Type

Trade

Requirements
Must have
• Colors should go with logo, blues...

```html
<!DOCTYPE html>
<html lang="en">
<head>
<meta charset="utf-8">
<title>Velun Tresk, PLLC — Home</title>
<link href="https://fonts.googleapis.com/css2?family=Arvo:wght@700&family=Delius&family=Open+Sans:wght@400;600;700&display=swap" rel="stylesheet">
<style>
:root{
  --navy-deep:#02031a;
  --brand-blue:#1a8fd8;
  --nav-blue:#1b2f7a;
  --ink:#444;
  --ink-soft:#5a5a5a;
  --paper:#f4f4f4;
  --band:#e6e6e6;
  --map:#1f2428;
  --white:#fff;
}
*{margin:0;padding:0;box-sizing:border-box}
html,body{width:1119px;height:1200px;overflow:hidden;background:var(--paper);font-family:"Open Sans",sans-serif;color:var(--ink)}
.page{position:relative;width:1119px;height:1200px}

/* header */
.site-header{position:absolute;top:0;left:0;width:100%;height:73px;background:#f7f7f7}
.brand{position:absolute;left:224px;top:12px;width:108px;height:54px;display:flex;flex-direction:column;align-items:center;justify-content:flex-end}
.brand-mark{width:24px;height:24px;border-radius:50%;background:var(--nav-blue);margin-bottom:6px}
.brand-name{font-size:9px;letter-spacing:.5px;color:#333;font-weight:600;white-space:nowrap}
.brand-divider{position:absolute;left:332px;top:8px;width:1px;height:58px;background:#ddd}
.main-nav{position:absolute;left:366px;top:29px;display:flex}
.main-nav a{font-size:10px;color:#222;text-decoration:none;padding:0 12px;position:relative;height:24px}
.main-nav a.active::after{content:"";position:absolute;left:0;right:0;bottom:0;height:3px;background:var(--nav-blue)}
.header-contact{position:absolute;right:229px;top:21px;text-align:right;font-size:13px;line-height:15px;color:#333}
.header-contact span{display:flex;align-items:center;justify-content:flex-end;gap:3px}
.header-contact svg{width:11px;height:11px;fill:var(--nav-blue)}

/* hero */
.hero{position:absolute;top:73px;left:0;width:100%;height:371px;background:linear-gradient(90deg,#02061e 0%,#071741 45%,#0b1f52 60%,#03081f 100%)}
.hero-photo{position:absolute;left:443px;top:0;width:491px;height:371px;background:radial-gradient(ellipse at 60% 40%,#2c4f8a 0%,#163464 45%,rgba(8,22,60,0) 80%)}
.hero-title{position:absolute;left:224px;top:96px;font-family:"Arvo",Georgia,serif;font-weight:700;font-size:38px;line-height:46px;color:var(--brand-blue);white-space:nowrap}
.hero-text{position:absolute;left:224px;top:191px;width:390px;font-size:12px;line-height:17px;font-weight:700;color:var(--white)}
.hero-button{position:absolute;left:224px;top:253px;width:80px;height:30px;border-radius:4px;background:linear-gradient(#f4f4f4,#c9c9c9);border:1px solid #aaa;font-size:12px;font-weight:600;color:#222;display:flex;align-items:center;justify-content:center}
.hero-arrow{position:absolute;top:172px;width:27px;height:27px;border-radius:50%;background:var(--white);display:flex;align-items:center;justify-content:center}
.hero-arrow svg{width:12px;height:12px;stroke:#111;stroke-width:3;fill:none}
.hero-arrow.prev{left:57px}.hero-arrow.next{left:1036px}

/* sections */
.section-title{font-family:"Delius",cursive;font-size:24px;color:var(--brand-blue);line-height:30px;letter-spacing:-.5px}
.section-lead{font-size:11.5px;line-height:13px;color:var(--ink-soft);margin-top:5px}
.why-us{position:absolute;top:444px;left:0;width:100%;height:266px;background:var(--paper)}
.why-photo{position:absolute;left:224px;top:22px;width:325px;height:221px;background:linear-gradient(120deg,#3b2412,#8a5a2c 55%,#2a1d16)}
.why-copy{position:absolute;left:560px;top:15px;width:330px}
.why-copy p.body{font-size:9px;line-height:12.6px;color:#555;margin-top:10px}
.why-copy a{color:var(--brand-blue);text-decoration:none}

.services{position:absolute;top:710px;left:0;width:100%;height:253px;background:var(--band)}
.services-copy{position:absolute;left:224px;top:17px;width:330px}
.service-list{list-style:none;margin-top:6px}
.service-list li{font-size:11px;line-height:17.2px;color:#555;display:flex;align-items:center;gap:4px}
.service-list li::before{content:"";border-left:4px solid var(--nav-blue);border-top:3px solid transparent;border-bottom:3px solid transparent}
.services-photo{position:absolute;left:563px;top:17px;width:326px;height:221px;background:linear-gradient(100deg,#f6f6f6 0%,#2a2c33 30%,#1a1b20 70%,#e9e9e9 100%)}

/* footer */
.contact-band{position:absolute;top:963px;left:0;width:100%;height:162px;background:var(--map)}
.contact-lines{position:absolute;top:20px;width:100%;text-align:center;font-size:17px;line-height:24px;color:var(--white)}
.social{position:absolute;top:112px;left:0;width:100%;display:flex;justify-content:center;gap:4px}
.social span{width:26px;height:26px;border-radius:50%;background:#2a6fb5}
.site-footer{position:absolute;top:1125px;left:0;width:100%;height:75px;background:var(--navy-deep)}
.copyright{position:absolute;left:224px;top:34px;font-size:9.5px;color:var(--white)}
.footer-brand{position:absolute;left:800px;top:12px;width:90px;display:flex;flex-direction:column;align-items:center}
.footer-brand .brand-mark{background:var(--white);margin-bottom:8px}
.footer-brand .brand-name{color:var(--white)}
</style>
</head>
<body>
<div class="page">
  <header class="site-header">
    <div class="brand"><span class="brand-mark"></span><span class="brand-name">VELUN TRESK, PLLC</span></div>
    <div class="brand-divider"></div>
    <nav class="main-nav">
      <a class="active">Home</a><a>About Velun</a><a>Practice Area</a><a>Lawyers</a><a>Case Study</a><a>Contact Us</a>
    </nav>
    <div class="header-contact">
      <span><svg viewBox="0 0 24 24"><path d="M6.6 10.8a15 15 0 0 0 6.6 6.6l2.2-2.2c.3-.3.7-.4 1-.2 1.1.4 2.3.6 3.6.6.6 0 1 .4 1 1V20c0 .6-.4 1-1 1A17 17 0 0 1 3 4c0-.6.4-1 1-1h3.5c.6 0 1 .4 1 1 0 1.3.2 2.5.6 3.6.1.3 0 .7-.2 1z"/></svg>555.014.2290</span>
      <span><svg viewBox="0 0 24 24"><path d="M12 2a7 7 0 0 0-7 7c0 5 7 13 7 13s7-8 7-13a7 7 0 0 0-7-7zm0 9.5A2.5 2.5 0 1 1 12 6.5a2.5 2.5 0 0 1 0 5z"/></svg>Our Map</span>
    </div>
  </header>

  <section class="hero">
    <div class="hero-photo" role="img" aria-label="Photo of a lawyer in a navy suit and tie"></div>
    <h1 class="hero-title">WE PROVIDE LEGAL<br>HELP FOR YOU!</h1>
    <p class="hero-text">The point of using Lorem Ipsum is that it has a more-or-less normal distribution of letters, as opposed to using 'Content here, content here making it look like readable English.</p>
    <div class="hero-button">Read More</div>
    <div class="hero-arrow prev"><svg viewBox="0 0 12 12"><path d="M8 1 3 6l5 5"/></svg></div>
    <div class="hero-arrow next"><svg viewBox="0 0 12 12"><path d="M4 1l5 5-5 5"/></svg></div>
  </section>

  <section class="why-us">
    <div class="why-photo" role="img" aria-label="Photo of a lawyer meeting a client across a desk"></div>
    <div class="why-copy">
      <h2 class="section-title">Why Us?</h2>
      <p class="section-lead">Lorem Ipsum iaking it look like readable English.Lorem Ipsum is that it has a more-or-less normal distribution</p>
      <p class="body">Lorem Ipsum is that it has a more-or-less normal distribution of letters, as opposed to using 'Content here, content here', making it look like readable English.Lorem Ipsum is that it has a more-or-less normal distribution of letters, as opposed.Lorem Ipsum is that it has a more-or-less normal distribution of letters, as opposed to using 'Content here, content here', making it look like readable English.Lorem Ipsum is that it has a more-or-less normal distribution of letters, as opposed.</p>
      <p class="body">Lorem Ipsum is that it has a more-or-less normal distribution of letters, as opposed to using 'Content here, content here', making it look like readable English.Lorem Ipsum is that it has a more-or-less normal distribution of letters, as opposed. <a>Read More ▸</a></p>
    </div>
  </section>

  <section class="services">
    <div class="services-copy">
      <h2 class="section-title">What WE Do ?</h2>
      <p class="section-lead">Lorem Ipsum iaking it look like readable English.Lorem Ipsum is that it has a more-or-less normal distribution.</p>
      <ul class="service-list">
        <li>Intellectual Property</li><li>Patents</li><li>Copyrights</li><li>Trademarks</li><li>Trade secrets</li><li>Healthcare Compliance</li><li>Elder law</li><li>Wills</li><li>Trusts</li>
      </ul>
    </div>
    <div class="services-photo" role="img" aria-label="Photo of a man in a dark suit and gold tie pointing forward"></div>
  </section>

  <section class="contact-band" role="img" aria-label="Faint street map background">
    <div class="contact-lines">
      <p>Address: Brennick Street . Suite 214 Halvor,NYC</p>
      <p>Phone: 5550 194 27</p>
      <p>Fax: 55501 948 30</p>
    </div>
    <div class="social"><span></span><span></span><span></span><span></span></div>
  </section>

  <footer class="site-footer">
    <p class="copyright">© 2013 Velun Tresk.PLL. All rights reserved.</p>
    <div class="footer-brand"><span class="brand-mark"></span><span class="brand-name">VELUN TRESK, PLLC</span></div>
  </footer>
</div>
</body>
</html>
```